Redesign of business card for Cedar Ridge Mechanical

We are looking for a new design for our business cards for Cedar Ridge Mechanical. We are a plumbing & HVAC construction company, operating on the West Coast of Canada and USA. Logo attached.
Industry/Entity Type
Construction - Plumbing & HVAC
Contact Information for Business Card
Name, address, phone numbers, email, website address
Look and feel
Each slider illustrates characteristics of the customer's brand and the style your logo design should communicate.

```html
<!DOCTYPE html>
<html lang="en">
<head>
<meta charset="utf-8">
<title>Cedar Ridge Mechanical – Business Card</title>
<link href="https://fonts.googleapis.com/css2?family=Poppins:wght@300;400;600&display=swap" rel="stylesheet">
<style>
  :root {
    --page: #3a3f45;
    --card-front: #1f1f21;
    --card-back: #202023;
    --pattern-a: #26262a;
    --pattern-b: #1c1c1f;
    --ink: #ffffff;
    --ink-soft: #d9d9d9;
  }
  * { box-sizing: border-box; margin: 0; padding: 0; }
  html, body {
    width: 1200px; height: 780px; overflow: hidden;
    background: var(--page);
    font-family: "Poppins", sans-serif;
    color: var(--ink);
  }
  .sheet {
    width: 1200px; height: 780px;
    display: flex; flex-direction: column;
    align-items: center; justify-content: center; gap: 40px;
  }
  .card {
    position: relative;
    width: 600px; height: 343px;
    border-radius: 4px;
    overflow: hidden;
    box-shadow: 0 10px 30px rgba(0,0,0,.35);
  }
  .card--front { background: var(--card-front); }
  .card--back { background: var(--card-back); }

  /* front */
  .brand {
    position: absolute; top: 38px; right: 40px;
    display: flex; align-items: center; gap: 12px;
  }
  .brand__square {
    width: 26px; height: 26px; background: var(--ink);
  }
  .brand__name {
    font-weight: 600; font-size: 20px; letter-spacing: .04em;
    text-transform: uppercase; line-height: 1;
  }
  .divider {
    position: absolute; top: 178px; left: 160px; right: 0;
    height: 1.5px; background: var(--ink);
  }
  .person {
    position: absolute; left: 36px; top: 140px;
  }
  .person__name { font-size: 31px; line-height: 1; white-space: nowrap; }
  .person__first { font-weight: 600; }
  .person__last { font-weight: 300; }
  .person__title {
    margin-top: 12px; font-size: 16px; font-weight: 300; color: var(--ink-soft);
  }
  .contact {
    position: absolute; right: 30px; top: 196px;
    text-align: right; font-size: 14px; font-weight: 300; line-height: 1.55;
  }
  .contact__address { margin-bottom: 12px; }
  .contact__row { display: flex; align-items: center; justify-content: flex-end; gap: 10px; }
  .contact__row svg { width: 13px; height: 13px; flex: none; }

  /* back */
  .pattern {
    position: absolute; inset: 0;
    background: linear-gradient(135deg, var(--pattern-a), var(--pattern-b));
  }
  .back-mark {
    position: absolute; left: 62%; top: 53%;
    transform: translate(-50%, -50%);
    font-weight: 600; font-size: 12px; letter-spacing: .05em;
    text-transform: uppercase; white-space: nowrap;
  }
</style>
</head>
<body>
<main class="sheet">
  <section class="card card--front" aria-label="Business card front">
    <div class="brand">
      <span class="brand__square"></span>
      <span class="brand__name">Cedar Ridge Mechanical</span>
    </div>

    <div class="person">
      <p class="person__name"><span class="person__first">Marta</span> <span class="person__last">Kovalen</span></p>
      <p class="person__title">Founder &amp; CEO</p>
    </div>
    <div class="divider"></div>

    <div class="contact">
      <p class="contact__address">1840 Harbor Lane Suite 300<br>Tacoma, WA 98402</p>
      <p class="contact__row">(253) 555-0147
        <svg viewBox="0 0 24 24" aria-hidden="true"><path fill="#fff" d="M6.6 10.8a15.1 15.1 0 0 0 6.6 6.6l2.2-2.2a1 1 0 0 1 1-.25 11.4 11.4 0 0 0 3.6.57 1 1 0 0 1 1 1V20a1 1 0 0 1-1 1A17 17 0 0 1 3 4a1 1 0 0 1 1-1h3.5a1 1 0 0 1 1 1c0 1.25.2 2.45.57 3.57a1 1 0 0 1-.25 1z"/></svg>
      </p>
      <p class="contact__row">info@cedarridgemech.com
        <svg viewBox="0 0 24 24" aria-hidden="true"><circle cx="12" cy="12" r="9.5" fill="none" stroke="#fff" stroke-width="2"/><path d="M2.5 12h19M12 2.5c3 3 3 16 0 19M12 2.5c-3 3-3 16 0 19" fill="none" stroke="#fff" stroke-width="1.6"/></svg>
      </p>
      <p class="contact__row">www.cedarridgemech.com
        <svg viewBox="0 0 24 24" aria-hidden="true"><rect x="2.5" y="5" width="19" height="14" rx="1.5" fill="none" stroke="#fff" stroke-width="2"/><path d="M3 6l9 7 9-7" fill="none" stroke="#fff" stroke-width="2"/></svg>
      </p>
    </div>
  </section>

  <section class="card card--back" aria-label="Business card back">
    <div class="pattern" role="img" aria-label="Repeating tone-on-tone monogram pattern covering the card back"></div>
    <span class="back-mark">Cedar Ridge Mechanical</span>
  </section>
</main>
</body>
</html>
```